business card design for a plumbing contractor

i need a double business card for a plumbing business, our initial service is residential Sewer Drain Cleaning.

Target Market(s)

other plumbing Business

Industry/Entity Type

Plumbing

Contact Information for Business Card

www.PipeworksTopMark.example- 5307218394-

Font styles to use
Serif

Colors
ec1f27
0455a3

```html
<!DOCTYPE html>
<html lang="en">
<head>
<meta charset="utf-8">
<title>Pipeworks TopMark – Business Card</title>
<link rel="stylesheet" href="https://fonts.googleapis.com/css2?family=Arimo:wght@400;700&display=swap">
<style>
  :root {
    --brand-red: #ec1f27;
    --brand-blue: #0455a3;
    --card-blue: #2a67a4;
    --band-blue: #2c609a;
    --ink: #222222;
    --paper: #ffffff;
    --stage: #2b2b2b;
  }
  * { box-sizing: border-box; margin: 0; padding: 0; }
  html, body { width: 1200px; height: 997px; overflow: hidden; }
  body {
    background: var(--stage);
    font-family: "Arimo", Arial, sans-serif;
    position: relative;
  }
  .card {
    position: absolute;
    width: 560px;
    height: 320px;
    border-radius: 22px;
    overflow: hidden;
  }
  .card-front {
    left: 90px; top: 110px;
    background: var(--card-blue);
    display: flex; align-items: center; justify-content: center; gap: 18px;
  }
  .front-mark {
    width: 46px; height: 46px; background: var(--paper); border-radius: 50%;
  }
  .front-name {
    color: var(--paper);
    font-weight: 700;
    font-size: 46px;
    line-height: 1;
  }
  .card-back {
    left: 550px; top: 480px;
    background: var(--paper);
  }
  .back-decoration {
    position: absolute; right: -40px; top: -30px;
    width: 300px; height: 300px; border-radius: 50%;
    background: var(--brand-red); opacity: 0.1;
  }
  .back-logo {
    position: absolute; left: 28px; top: 32px;
    display: flex; align-items: center; gap: 10px;
  }
  .back-logo .mark { width: 24px; height: 24px; border-radius: 50%; background: var(--brand-red); }
  .back-logo .name { color: #555555; font-weight: 700; font-size: 26px; }
  .holder {
    position: absolute; left: 0; right: 0; top: 118px; text-align: center;
  }
  .holder-name { color: var(--brand-red); font-weight: 700; font-size: 20px; letter-spacing: 0.5px; }
  .holder-role { color: var(--brand-blue); font-size: 15px; margin-top: 2px; }
  .contact {
    position: absolute; left: 28px; bottom: 66px;
    list-style: none; font-size: 16px; color: var(--ink);
  }
  .contact li { display: flex; align-items: center; gap: 12px; margin-top: 8px; }
  .contact svg { width: 18px; height: 18px; flex: none; }
  .website {
    position: absolute; right: 24px; bottom: 82px;
    color: var(--brand-red); font-weight: 700; font-size: 15px;
  }
  .service-band {
    position: absolute; left: 0; right: 0; bottom: 0; height: 50px;
    background: var(--band-blue);
    border-top: 3px solid var(--brand-red);
    color: var(--paper); font-size: 14px; letter-spacing: 0.6px;
    display: flex; align-items: center; justify-content: center;
  }
</style>
</head>
<body>
  <section class="card card-front" aria-label="Card front">
    <span class="front-mark"></span>
    <span class="front-name">Pipeworks TopMark</span>
  </section>

  <section class="card card-back" aria-label="Card back">
    <div class="back-decoration"></div>
    <div class="back-logo">
      <span class="mark"></span>
      <span class="name">Pipeworks TopMark</span>
    </div>
    <div class="holder">
      <div class="holder-name">MARCO DELVANE</div>
      <div class="holder-role">Director</div>
    </div>
    <ul class="contact">
      <li>
        <svg viewBox="0 0 20 20" aria-hidden="true"><circle cx="10" cy="10" r="10" fill="var(--brand-blue)"/><path d="M6.5 5.5c.6-.6 1.4-.5 1.8.1l.8 1.3c.3.5.2 1-.2 1.4l-.5.5c.5 1.2 1.5 2.2 2.7 2.7l.5-.5c.4-.4.9-.5 1.4-.2l1.3.8c.6.4.7 1.2.1 1.8-1 1-2.6 1-4.4-.3-1.2-.9-2.2-1.9-3.1-3.1C5.5 8.1 5.5 6.5 6.5 5.5z" fill="#fff"/></svg>
        5307218394
      </li>
      <li>
        <svg viewBox="0 0 20 20" aria-hidden="true"><circle cx="10" cy="10" r="10" fill="var(--brand-blue)"/><rect x="5" y="6.5" width="10" height="7" rx="1" fill="#fff"/><path d="M5.5 7l4.5 3.5L14.5 7" stroke="var(--brand-blue)" stroke-width="1" fill="none"/></svg>
        Dispatch@PipeworksTopMark.example
      </li>
    </ul>
    <div class="website">www.PipeworksTopMark.example</div>
    <div class="service-band">SEWER DRAIN CLEANING, MAINTENANCE, TRENCHLESS PIPE INSTALLS</div>
  </section>
</body>
</html>
```